Sales Proposal Template Design

I sell Internet Marketing services; including search engine optimization, search engine marketing, social media, websites, mobile websites, email and video.

I produce a proposal for each prospective client. Some include SEO and PPC. Other include more services or less services. The purpose of this project is to create a template in MS Word or Power Point. I will add standard content for each product with different pricing for different projects.

I want one page for each product or service I will be presenting the the proposal. I can then use just one page or multiple pages to build the full proposal.

Once I am finished I will convert the single sheets into a PDF document to print or send to the client via email.

I am part of a the This is a KVO Franchise http://www.kvoglobe-example.com/ you can see the corporate colors and design on this website.

I would like both a vertical and horizontal orientation template.

Target Market(s)

Prospects and buyers that request information and pricing.

Industry/Entity Type

Internet

Requirements
Must have
• Must have the KVO logo and be consistent with their colors and design feel.

I need a lot of open space for content copy.

The template needs to be in MS Word or Power Point.
Nice to have
• A front cover design that matches the inside page template would be nice to have.

```html
<!DOCTYPE html>
<html lang="en">
<head>
<meta charset="utf-8">
<title>Service Page Template</title>
<link rel="stylesheet" href="https://fonts.googleapis.com/css2?family=PT+Sans&family=Questrial&display=swap">
<style>
  :root {
    --canvas: #ffffff;
    --page: #ffffff;
    --heading-blue: #1d4b8c;
    --body-blue: #1b3d78;
    --navy: #0a2a54;
    --ocean: #1b6fb0;
    --sky: #5aa9dd;
    --haze: rgba(196, 212, 230, 0.35);
    --globe-light: #eef8fe;
    --globe-mid: #a9d6f2;
    --globe-deep: #4f9fd6;
  }
  * { margin: 0; padding: 0; box-sizing: border-box; }
  html, body {
    width: 1200px;
    height: 900px;
    overflow: hidden;
    background: var(--canvas);
  }
  .page {
    position: absolute;
    left: 133px;
    top: 102px;
    width: 933px;
    height: 698px;
    background: var(--page);
    box-shadow: 6px 8px 10px rgba(0, 0, 0, 0.28);
    overflow: hidden;
  }
  .line-texture {
    position: absolute;
    inset: 0;
    background: linear-gradient(155deg, rgba(255,255,255,0) 40%, var(--haze) 58%, rgba(255,255,255,0) 78%);
  }
  .wave-band {
    position: absolute;
    left: 0;
    top: 488px;
    width: 933px;
    height: 210px;
    background: linear-gradient(to bottom, rgba(255,255,255,0) 0%, var(--sky) 38%, var(--ocean) 62%, var(--navy) 100%);
  }
  .globe {
    position: absolute;
    left: 617px;
    top: 438px;
    width: 188px;
    height: 188px;
    border-radius: 50%;
    background: radial-gradient(circle at 42% 35%, var(--globe-light) 0%, var(--globe-mid) 60%, var(--globe-deep) 100%);
  }
  .content {
    position: absolute;
    left: 95px;
    top: 96px;
    width: 760px;
    color: var(--body-blue);
  }
  .subheading {
    font-family: "PT Sans", sans-serif;
    font-weight: 400;
    font-size: 37px;
    letter-spacing: 0.3px;
    color: var(--heading-blue);
    line-height: 1;
    margin-bottom: 36px;
  }
  .body-copy p {
    font-family: "Questrial", sans-serif;
    font-size: 13.6px;
    line-height: 17px;
    margin-bottom: 17px;
    white-space: nowrap;
  }
</style>
</head>
<body>
  <div class="page">
    <div class="line-texture" role="img" aria-label="Fine diagonal line texture"></div>
    <div class="wave-band" role="img" aria-label="Flowing red and blue wave ribbons over a deep blue base"></div>
    <div class="globe" role="img" aria-label="Glass globe showing the Americas"></div>

    <div class="content">
      <h2 class="subheading">SUBHEADING</h2>
      <div class="body-copy">
        <p>"Lorem ipsum dolor sit amet, consectetur adipisicing elit, sed do eiusmod tempor incididunt ut labore et dolore<br>magna aliqua. Ut enim ad minim veniam, quis nostrud exercitation ullamco laboris nisi ut aliquip ex ea commodo<br>consequat. Duis aute irure dolor in reprehenderit in voluptate velit esse cillum dolore eu fugiat nulla pariatur.</p>
        <p>Excepteur sint occaecat cupidatat non proident, sunt in culpa qui officia deserunt mollit anim id est laborum."<br>&nbsp;"At vero eos et accusamus et iusto odio dignissimos ducimus qui blanditiis praesentium voluptatum deleniti atque<br>corrupti quos dolores et quas molestias excepturi sint occaecati cupiditate non provident, similique sunt in culpa<br>qui officia deserunt mollitia animi, id est laborum et dolorum fuga.</p>
        <p>Et harum quidem rerum facilis est et expedita distinctio. Nam libero tempore, cum soluta nobis est eligendi optio<br>cumque nihil impedit quo minus id quod maxime placeat facere possimus, omnis voluptas assumenda est, omnis<br>dolor repellendus. Temporibus autem quibusdam et aut officiis debitis aut rerum necessitatibus saepe eveniet ut<br>et voluptates repudiandae sint et molestiae non recusandae. Itaque earum rerum hic tenetur a sapiente delec-<br>tus, ut aut reiciendis voluptatibus maiores alias consequatur aut perferendis doloribus asperiores repellat."</p>
      </div>
    </div>
  </div>
</body>
</html>
```